Road Construction Company needs business cards

We would like a new business card designed for our business.

We're a road construction company based in Qld, Australia.

Can the business card please have the following information on it.

Name: Warren Halbeck
Position: General Manager
Phone: 0472 915 348
Email: Warren.halbeck@tovrin.com.au
Address: 87 Marrow Ave, Pendlebay, QLD, 4023
Website: www.tovrin.com.au

Visually we'd like the card to be professional and simple.

Attached is our logo.

Our website is www.tovrin.com.au

Target Market(s)

Men aged 25-60

Contact Information for Business Card

As listed in project description

Font styles to use
Serif

Requirements
Must have
• Large logo on back of card

```html
<!DOCTYPE html>
<html lang="en">
<head>
<meta charset="utf-8">
<title>Tovrin Road Construction – Business Card</title>
<link rel="stylesheet" href="https://fonts.googleapis.com/css2?family=Open+Sans:wght@400;600;700;800&display=swap">
<style>
  :root {
    --navy: #1456a6;
    --sky: #46aadc;
    --paper: #ffffff;
    --ink: #111111;
    --stage: #232323;
  }
  * { box-sizing: border-box; margin: 0; padding: 0; }
  html, body {
    width: 1200px;
    height: 780px;
    overflow: hidden;
    background: var(--stage);
    font-family: "Open Sans", Arial, sans-serif;
  }
  .sheet {
    width: 1200px;
    height: 780px;
    display: flex;
    align-items: center;
    justify-content: center;
    gap: 40px;
  }
  .card {
    position: relative;
    width: 540px;
    height: 320px;
    border-radius: 22px;
    overflow: hidden;
    background: var(--paper);
  }
  .card__swoosh {
    position: absolute;
    inset: 0;
    width: 100%;
    height: 100%;
  }
  .swoosh--navy { fill: var(--navy); }
  .swoosh--sky { fill: var(--sky); }

  .wordmark {
    position: absolute;
    color: var(--navy);
    font-weight: 800;
    line-height: 1;
  }
  .wordmark__name { display: block; letter-spacing: 1px; }
  .wordmark__tag { display: block; text-transform: uppercase; }

  .card--front .wordmark { left: 110px; top: 110px; }
  .card--front .wordmark__name { font-size: 84px; }
  .card--front .wordmark__tag { font-size: 15px; letter-spacing: 9.5px; margin-top: 6px; }

  .card--back .wordmark { left: 46px; top: 132px; }
  .card--back .wordmark__name { font-size: 50px; }
  .card--back .wordmark__tag { font-size: 9px; letter-spacing: 5.6px; margin-top: 4px; }

  .divider {
    position: absolute;
    left: 272px;
    top: 58px;
    width: 1px;
    height: 170px;
    background: var(--ink);
  }
  .contact {
    position: absolute;
    left: 292px;
    top: 62px;
    color: var(--ink);
  }
  .contact__name {
    font-size: 25px;
    font-weight: 700;
    color: var(--navy);
    line-height: 1.1;
  }
  .contact__role {
    font-size: 14px;
    font-weight: 600;
    margin-bottom: 14px;
  }
  .contact__list { list-style: none; }
  .contact__item {
    display: flex;
    align-items: center;
    gap: 7px;
    font-size: 12.5px;
    line-height: 1.75;
  }
  .contact__icon { width: 12px; height: 12px; fill: var(--sky); flex: none; }
  .address {
    position: absolute;
    right: 76px;
    bottom: 46px;
    font-size: 15px;
    color: var(--ink);
  }
</style>
</head>
<body>
<main class="sheet">

  <section class="card card--front" aria-label="Card front">
    <svg class="card__swoosh" viewBox="0 0 540 320" preserveAspectRatio="none" aria-hidden="true">
      <path class="swoosh--navy" d="M0 0 H150 C70 40 20 110 0 200 Z"/>
      <path class="swoosh--sky" d="M540 120 V320 H380 C470 270 520 200 540 120 Z"/>
    </svg>
    <div class="wordmark">
      <span class="wordmark__name">TOVRIN</span>
      <span class="wordmark__tag">Road Construction</span>
    </div>
  </section>

  <section class="card card--back" aria-label="Card back">
    <svg class="card__swoosh" viewBox="0 0 540 320" preserveAspectRatio="none" aria-hidden="true">
      <path class="swoosh--navy" d="M0 0 H130 C60 40 18 110 0 190 Z"/>
      <path class="swoosh--sky" d="M540 115 V320 H400 C480 265 525 195 540 115 Z"/>
    </svg>

    <div class="wordmark">
      <span class="wordmark__name">TOVRIN</span>
      <span class="wordmark__tag">Road Construction</span>
    </div>

    <div class="divider"></div>

    <div class="contact">
      <p class="contact__name">Warren Halbeck</p>
      <p class="contact__role">General Manager</p>
      <ul class="contact__list">
        <li class="contact__item">
          <svg class="contact__icon" viewBox="0 0 24 24" aria-hidden="true"><path d="M6.6 10.8a15.1 15.1 0 0 0 6.6 6.6l2.2-2.2c.3-.3.7-.4 1-.2 1.1.4 2.3.6 3.6.6.6 0 1 .4 1 1V20c0 .6-.4 1-1 1A17 17 0 0 1 3 4c0-.6.4-1 1-1h3.5c.6 0 1 .4 1 1 0 1.3.2 2.5.6 3.6.1.3 0 .7-.2 1z"/></svg>
          <span>0472 915 348</span>
        </li>
        <li class="contact__item">
          <svg class="contact__icon" viewBox="0 0 24 24" aria-hidden="true"><path d="M12 2a10 10 0 1 0 0 20 10 10 0 0 0 0-20zm6.9 6h-2.9a15.7 15.7 0 0 0-1.4-3.6A8 8 0 0 1 18.9 8zM12 4c.8 1.2 1.5 2.5 1.9 4h-3.8c.4-1.5 1.1-2.8 1.9-4zM4.3 14a8 8 0 0 1 0-4h3.4a16.5 16.5 0 0 0 0 4zm.8 2h2.9c.3 1.3.8 2.5 1.4 3.6A8 8 0 0 1 5.1 16zM8 8H5.1a8 8 0 0 1 4.3-3.6C8.8 5.5 8.3 6.7 8 8zm4 12c-.8-1.2-1.5-2.5-1.9-4h3.8c-.4 1.5-1.1 2.8-1.9 4zm2.3-6H9.7a14.7 14.7 0 0 1 0-4h4.6a14.7 14.7 0 0 1 0 4zm.3 5.6c.6-1.1 1.1-2.3 1.4-3.6h2.9a8 8 0 0 1-4.3 3.6zM16.3 14a16.5 16.5 0 0 0 0-4h3.4a8 8 0 0 1 0 4z"/></svg>
          <span>www.tovrin.com.au</span>
        </li>
        <li class="contact__item">
          <svg class="contact__icon" viewBox="0 0 24 24" aria-hidden="true"><path d="M20 4H4a2 2 0 0 0-2 2v12a2 2 0 0 0 2 2h16a2 2 0 0 0 2-2V6a2 2 0 0 0-2-2zm0 4-8 5-8-5V6l8 5 8-5z"/></svg>
          <span>Warren.halbeck@tovrin.com.au</span>
        </li>
      </ul>
    </div>

    <p class="address">87 Marrow Ave, Pendlebay, QLD, 4023</p>
  </section>

</main>
</body>
</html>
```